Veluxa Bone & Motion Business Card

Need a business card using the logo provided. I want brand side of the card to be grey with the logo in the center of the card in white.

On the other side I leave to the designers

Target Market(s)

Personal Injury Attorneys

Industry/Entity Type

Medical

Contact Information for Business Card

Name, CEO. Cell Phone, (Coral Vale, Address, Phone) (Marsh Point, Address, Phone) (Oakhaven, Address, Phone)

Colors

Designer to choose only greyscale colors for use in the design.

Requirements
Must have
• Logo by itself on one side

```html
<!DOCTYPE html>
<html lang="en">
<head>
<meta charset="utf-8">
<title>Veluxa Bone &amp; Motion Business Card</title>
<link rel="stylesheet" href="https://fonts.googleapis.com/css2?family=Montserrat:wght@400;500;600&display=swap">
<style>
  :root {
    --backdrop: #b0b0ac;
    --card-dark: #242526;
    --band-grey: #7b7f84;
    --stripe-grey: #bcc0c3;
    --text-light: #f4f5f6;
    --wordmark-grey: #9a9ea2;
    --logo-grey: #d2d4d6;
    --edge-grey: #6c6f72;
  }
  * { margin: 0; padding: 0; box-sizing: border-box; }
  html, body {
    width: 1200px; height: 801px; overflow: hidden;
    background: var(--backdrop);
    font-family: "Montserrat", sans-serif;
  }
  .stage {
    width: 1200px; height: 801px;
    display: flex; align-items: center; justify-content: center; gap: 40px;
  }
  .card {
    position: relative;
    width: 540px; height: 309px;
    border-radius: 16px;
    overflow: hidden;
    background: var(--card-dark);
    box-shadow: 0 0 0 1px var(--edge-grey), 0 14px 30px rgba(0,0,0,.28);
  }
  /* info side: slanted band with notch tab near the left edge */
  .band-stripe, .info-band {
    position: absolute; inset: 0;
  }
  .band-stripe {
    background: var(--stripe-grey);
    clip-path: polygon(0 156px, 70px 156px, 78px 148px, 540px 122px, 540px 309px, 0 309px);
  }
  .info-band {
    background: var(--band-grey);
    clip-path: polygon(0 163px, 74px 163px, 82px 155px, 540px 129px, 540px 309px, 0 309px);
  }
  .wordmark {
    position: absolute;
    font-weight: 500;
    text-transform: uppercase;
    line-height: 1;
    white-space: nowrap;
  }
  .wordmark .main { display: block; letter-spacing: 6px; }
  .wordmark .sub { display: block; letter-spacing: 7px; margin-top: 6px; }
  .info-side .wordmark {
    left: 110px; top: 36px;
    color: var(--wordmark-grey);
  }
  .info-side .wordmark .main { font-size: 46px; }
  .info-side .wordmark .sub { font-size: 19px; padding-left: 44px; }

  .person {
    position: absolute; left: 40px; top: 178px;
    color: var(--text-light);
  }
  .person-name { font-size: 19px; font-weight: 600; letter-spacing: .5px; }
  .person-role { font-size: 12px; margin-top: 2px; }
  .contact-list { list-style: none; margin-top: 8px; }
  .contact-list li {
    display: flex; align-items: center; gap: 6px;
    font-size: 12.5px; line-height: 18px;
  }
  .contact-list svg { width: 11px; height: 11px; flex: none; }

  .offices {
    position: absolute; right: 24px; top: 152px;
    text-align: right; color: var(--text-light);
    font-size: 11.5px; line-height: 15px;
  }
  .office + .office { margin-top: 4px; }
  .office-phone { font-weight: 600; }

  /* brand side */
  .brand-side .wordmark {
    left: 50%; top: 50%;
    transform: translate(-50%, -50%);
    color: var(--logo-grey);
  }
  .brand-side .wordmark .main { font-size: 62px; letter-spacing: 8px; }
  .brand-side .wordmark .sub { font-size: 25px; letter-spacing: 9px; padding-left: 6px; margin-top: 8px; }
</style>
</head>
<body>
<main class="stage">
  <section class="card info-side" aria-label="Contact side">
    <div class="band-stripe"></div>
    <div class="info-band"></div>
    <div class="wordmark">
      <span class="main">Veluxa</span>
      <span class="sub">Bone &amp; Motion</span>
    </div>
    <div class="person">
      <p class="person-name">DORIAN WALSH</p>
      <p class="person-role">CEO</p>
      <ul class="contact-list">
        <li>
          <svg viewBox="0 0 12 12" fill="currentColor" aria-hidden="true"><path d="M2.5 1h2l1 2.6-1.3.9a6.5 6.5 0 0 0 3.3 3.3l.9-1.3L11 7.5v2A1.5 1.5 0 0 1 9.5 11 8.5 8.5 0 0 1 1 2.5 1.5 1.5 0 0 1 2.5 1z"/></svg>
          555-014-2210
        </li>
        <li>
          <svg viewBox="0 0 12 12" fill="none" stroke="currentColor" stroke-width="1.2" aria-hidden="true"><rect x="1" y="2.5" width="10" height="7" rx="1"/><path d="M1.3 3l4.7 3.6L10.7 3"/></svg>
          hello@veluxamotion.com
        </li>
        <li>
          <svg viewBox="0 0 12 12" fill="none" stroke="currentColor" stroke-width="1.1" aria-hidden="true"><circle cx="6" cy="6" r="5"/><ellipse cx="6" cy="6" rx="2.2" ry="5"/><path d="M1 6h10"/></svg>
          veluxamotion.com
        </li>
      </ul>
    </div>
    <div class="offices">
      <p class="office">Coral Vale, City in Florida<br><span class="office-phone">P : +330 5550-0101</span></p>
      <p class="office">Marsh Point, City in Florida<br><span class="office-phone">P : +330 5550-0102</span></p>
      <p class="office">Oakhaven, City in Florida<br><span class="office-phone">P : +330 5550-0103</span></p>
    </div>
  </section>

  <section class="card brand-side" aria-label="Brand side">
    <div class="wordmark">
      <span class="main">Veluxa</span>
      <span class="sub">Bone &amp; Motion</span>
    </div>
  </section>
</main>
</body>
</html>
```